Business cards to launch an education platform

Hi,
I am looking at having new business cards designed.
I am a startup, developing a web platform for schools and university, the education world. It's an online assessment system.
I would like a card that looks classy, and that is using the colors and the font of my logo.

I have attached:
1) my logo
2) A business card that I have designed quickly so you can have all the information required in the card, but I really don't like it.
3) The font that I am using (Lato Regular) to design my web platform
4) Some screenshots of my web platform so you can have a look at the style that I have.

Target Market(s)

Major market: Education system: Schools and university
Minor markets: Business in general

Industry/Entity Type

Business

Contact Information for Business Card

Clara Fenwick
Director

M: 0437 518 902
E: clara.fenwick@amberLoomSystems.com.au

Requirements
Must have
• The colors of my logo

```html
<!DOCTYPE html>
<html lang="en">
<head>
<meta charset="utf-8">
<title>Amber Loom systems – Business Cards</title>
<link rel="stylesheet" href="https://fonts.googleapis.com/css2?family=Lato:wght@400&family=Roboto+Condensed:wght@400;500&display=swap">
<style>
  :root {
    --backdrop: #8f9092;
    --card: #eceded;
    --navy: #123f73;
    --band-dark: #0a4690;
    --band-light: #1a67bc;
    --accent-line: #2aa7df;
    --mark: #1a5fae;
    --white: #ffffff;
  }
  * { margin: 0; padding: 0; box-sizing: border-box; }
  html, body {
    width: 1105px;
    height: 1200px;
    overflow: hidden;
    background: var(--backdrop);
  }
  .canvas {
    position: relative;
    width: 1105px;
    height: 1200px;
  }
  .card {
    position: absolute;
    left: 182px;
    width: 746px;
    height: 425px;
    background: var(--card);
    overflow: hidden;
  }
  .card--front { top: 120px; }
  .card--back { top: 637px; }

  .card__shapes {
    position: absolute;
    inset: 0;
    width: 746px;
    height: 425px;
  }

  .brand {
    position: absolute;
    display: flex;
    align-items: center;
    font-family: "Lato", sans-serif;
    font-weight: 400;
    color: var(--navy);
  }
  .brand__square {
    width: 100px;
    height: 100px;
    background: var(--mark);
    flex: none;
  }
  .brand__name {
    line-height: 1.05;
    letter-spacing: 2px;
  }
  .brand__name span { display: block; }

  .card--front .brand {
    left: 165px;
    top: 90px;
    gap: 26px;
  }
  .card--front .brand__name .brand__line-1 { font-size: 42px; }
  .card--front .brand__name .brand__line-2 { font-size: 27px; letter-spacing: 2.5px; }

  .card--back .brand {
    left: 0;
    width: 746px;
    top: 130px;
    flex-direction: column;
    gap: 22px;
    text-align: center;
  }
  .card--back .brand__square { width: 106px; height: 106px; }
  .card--back .brand__name .brand__line-1 { font-size: 39px; letter-spacing: 3px; }
  .card--back .brand__name .brand__line-2 { font-size: 27px; letter-spacing: 2.5px; }

  .contact {
    position: absolute;
    left: 42px;
    top: 300px;
    list-style: none;
    font-family: "Roboto Condensed", sans-serif;
    font-size: 18px;
    color: var(--white);
  }
  .contact__item {
    display: flex;
    align-items: center;
    gap: 12px;
    height: 28.5px;
  }
  .contact__icon {
    width: 16px;
    height: 16px;
    flex: none;
  }

  .person {
    position: absolute;
    right: 49px;
    top: 298px;
    text-align: right;
    font-family: "Roboto Condensed", sans-serif;
    color: var(--white);
  }
  .person__name {
    font-size: 34px;
    font-weight: 500;
    line-height: 1.1;
  }
  .person__role {
    font-size: 24px;
    font-weight: 500;
    line-height: 1.3;
  }
</style>
</head>
<body>
<div class="canvas">

  <section class="card card--front" aria-label="Business card front">
    <svg class="card__shapes" viewBox="0 0 746 425" aria-hidden="true">
      <defs>
        <radialGradient id="bandGlow" cx="0.5" cy="0.55" r="0.75">
          <stop offset="0" stop-color="var(--band-light)"/>
          <stop offset="1" stop-color="var(--band-dark)"/>
        </radialGradient>
      </defs>
      <polyline points="0,255 616,255 642,279 668,255 746,255" fill="none" stroke="var(--accent-line)" stroke-width="3"/>
      <path d="M0 262 H620 L642 284 L664 262 H746 V425 H0 Z" fill="url(#bandGlow)"/>
    </svg>

    <div class="brand">
      <div class="brand__square"></div>
      <div class="brand__name">
        <span class="brand__line-1">AMBER</span>
        <span class="brand__line-2">Loom systems</span>
      </div>
    </div>

    <ul class="contact">
      <li class="contact__item">
        <svg class="contact__icon" viewBox="0 0 16 16" aria-hidden="true">
          <rect x="4" y="1" width="8" height="14" rx="1.5" fill="none" stroke="#fff" stroke-width="1.6"/>
          <rect x="6.5" y="12" width="3" height="1.2" fill="#fff"/>
        </svg>
        <span>0437 518 902</span>
      </li>
      <li class="contact__item">
        <svg class="contact__icon" viewBox="0 0 16 16" aria-hidden="true">
          <rect x="1" y="3.5" width="14" height="9" fill="#fff"/>
          <polyline points="1,3.5 8,9 15,3.5" fill="none" stroke="var(--band-dark)" stroke-width="1.2"/>
        </svg>
        <span>clara.fenwick@amberLoomSystems.com.au</span>
      </li>
      <li class="contact__item">
        <svg class="contact__icon" viewBox="0 0 16 16" aria-hidden="true">
          <circle cx="8" cy="8" r="6.8" fill="#fff"/>
          <path d="M4 5 Q6 4 7 6 Q6 8 8 9 Q9 11 7 13 M10 3 Q12 5 11 7 Q13 8 14 10" fill="none" stroke="var(--band-dark)" stroke-width="1.2"/>
        </svg>
        <span>www.amberLoomSystems.com.au</span>
      </li>
    </ul>

    <div class="person">
      <p class="person__name">Clara Fenwick</p>
      <p class="person__role">Director</p>
    </div>
  </section>

  <section class="card card--back" aria-label="Business card back">
    <div class="brand">
      <div class="brand__square"></div>
      <div class="brand__name">
        <span class="brand__line-1">AMBER</span>
        <span class="brand__line-2">Loom systems</span>
      </div>
    </div>
  </section>

</div>
</body>
</html>
```